Roofing Contractor business card redesign

I want to redesign my business card with a fresh, eye catching concept

Target Market(s)

Residential Roofing Clients, potential employees, and subcontractors.

Industry/Entity Type

Business

Colors

Designer to choose colors to be used in the design.

Requirements
Nice to have
• I just want something that's more pleasing to the eye. You can use a combination of either / or of my logos.

```html
<!DOCTYPE html>
<html lang="en">
<head>
<meta charset="utf-8">
<title>Stout Crew General Contractors – Business Card</title>
<link rel="stylesheet" href="https://fonts.googleapis.com/css2?family=Rubik:wght@400;500;700;800&display=swap">
<style>
  :root {
    --backdrop: #d9d6d3;
    --card: #ecebeb;
    --card-edge: #ffffff;
    --ink: #2b2421;
    --ink-soft: #3a3330;
    --accent: #e8611c;
    --accent-warm: #f29a2e;
    --art-deep: #3b2a22;
    --art-mid: #c8552a;
    --art-light: #f3b43a;
  }
  * { margin: 0; padding: 0; box-sizing: border-box; }
  html, body {
    width: 1200px;
    height: 969px;
    overflow: hidden;
    background: var(--backdrop);
    font-family: "Rubik", sans-serif;
  }
  .business-card {
    position: absolute;
    left: 162px;
    top: 235px;
    width: 875px;
    height: 498px;
    border-radius: 22px;
    background: var(--card);
    border: 2px solid var(--card-edge);
    overflow: hidden;
    color: var(--ink);
  }
  .company-name {
    position: absolute;
    left: 48px;
    top: 22px;
    font-size: 60px;
    font-weight: 800;
    letter-spacing: -1.5px;
    line-height: 1;
    color: var(--ink);
  }
  .company-type {
    position: absolute;
    left: 50px;
    top: 103px;
    font-size: 22px;
    font-weight: 700;
    color: var(--ink);
  }
  .name-marker {
    position: absolute;
    left: 0;
    top: 145px;
    width: 11px;
    height: 92px;
    background: linear-gradient(var(--accent-warm), var(--accent));
  }
  .contact-name {
    position: absolute;
    left: 50px;
    top: 146px;
    font-size: 35px;
    font-weight: 500;
    color: var(--accent);
    text-transform: uppercase;
    letter-spacing: 0.3px;
  }
  .credentials, .address, .contact-lines {
    position: absolute;
    left: 50px;
    font-size: 20px;
    font-weight: 400;
    line-height: 27.5px;
    color: var(--ink-soft);
  }
  .credentials { top: 195px; }
  .address { top: 262px; }
  .contact-lines { top: 355px; }
  .crew-illustration {
    position: absolute;
    left: 398px;
    top: 30px;
    width: 464px;
    height: 464px;
  }
</style>
</head>
<body>
  <div class="business-card">
    <div class="company-name">Stout Crew</div>
    <div class="company-type">General Contractors, Inc.</div>

    <div class="name-marker"></div>
    <div class="contact-name">Dale Marrow</div>
    <div class="credentials">
      Hallet Certified Roof Inspector<br>
      Licensed Property Adjuster
    </div>

    <div class="address">
      4810 Cedar Bend Road<br>
      Suite 118<br>
      Garland, TX 75040
    </div>

    <div class="contact-lines">
      Office: (972) 555-0140<br>
      Mobile/Text: (972) 555-0187<br>
      dale@stoutcrewtx.com<br>
      www.stoutcrewtx.com
    </div>

    <svg class="crew-illustration" viewBox="0 0 464 464" role="img"
         aria-label="Circular illustration of three roofing workers with tools in front of a golden roof">
      <defs>
        <radialGradient id="crewTones" cx="50%" cy="40%" r="60%">
          <stop offset="0%" stop-color="var(--art-light)"/>
          <stop offset="55%" stop-color="var(--art-mid)"/>
          <stop offset="100%" stop-color="var(--art-deep)"/>
        </radialGradient>
      </defs>
      <circle cx="232" cy="232" r="230" fill="url(#crewTones)"/>
    </svg>
  </div>
</body>
</html>
```